Irrigation Business needs their business cards modernised and revamped

I would like to keep my current logo, colours and revamp the format of the card.

I would like the card to be clean yet important.

Im not sure if you include texture but i would like the named logo to be indented into the card etc.

show me something alive and free something thats clinical to the point yet has a feel of achievement. i would like people to go nice card.

Target Market(s)

high end clients, corporate, sports field manger, the guys that make the decisions

Industry/Entity Type

Business

Contact Information for Business Card

nformation to be included

Dean Harlow (Director)
0487305526
dean@kolvat.biz
www.kestonfieldworks.com

instagram logo
google logo
facebook logo

Colors

Designer to choose colors to be used in the design.

Requirements
Nice to have
• indentations a really nice feel to the card good texture

```html
<!DOCTYPE html>
<html lang="en">
<head>
<meta charset="utf-8">
<title>Keston Fieldworks – Business Card</title>
<link href="https://fonts.googleapis.com/css2?family=Montserrat:wght@700&family=Open+Sans:wght@400;700&display=swap" rel="stylesheet">
<style>
  :root{
    --bg:#e4e6e9;
    --blue-light:#4ba6de;
    --blue-deep:#2c68b0;
    --brand-blue:#2f5fa8;
    --brand-green:#3aa866;
    --rule:#8cc7ea;
    --paper:#f7f8f8;
    --ink:#555a60;
    --white:#ffffff;
  }
  *{box-sizing:border-box;margin:0;padding:0}
  html,body{width:1200px;height:900px;overflow:hidden}
  body{
    background:var(--bg);
    font-family:"Open Sans",Arial,sans-serif;
    display:flex;flex-direction:column;align-items:center;justify-content:center;gap:56px;
  }
  .card{
    width:660px;height:378px;position:relative;overflow:hidden;
    box-shadow:0 10px 26px rgba(0,0,0,.18);
  }
  /* back side */
  .card-back{
    background:linear-gradient(110deg,var(--blue-light) 0%,var(--blue-deep) 62%,var(--blue-deep) 100%);
    display:flex;flex-direction:column;align-items:center;justify-content:center;gap:22px;
  }
  .brand{display:flex;align-items:center;gap:16px}
  .brand-dot{border-radius:50%;flex:none}
  .brand-name{
    font-family:"Montserrat",Arial,sans-serif;font-weight:700;letter-spacing:.5px;text-transform:uppercase;
  }
  .card-back .brand-dot{width:70px;height:70px;background:var(--white)}
  .card-back .brand-name{color:var(--white);font-size:34px}
  .social{display:flex;gap:10px}
  .social span{width:20px;height:20px;border-radius:50%;background:var(--white)}
  /* front side */
  .card-front{background:var(--paper)}
  .card-front .brand{position:absolute;right:52px;top:70px}
  .card-front .brand-dot{width:58px;height:58px;background:var(--blue-light)}
  .card-front .brand-name{color:var(--brand-blue);font-size:27px}
  .rule{position:absolute;left:52px;right:52px;top:162px;height:1px;background:var(--rule)}
  .person{position:absolute;left:52px;top:214px}
  .person-name{color:var(--brand-blue);font-weight:700;font-size:17px;text-transform:uppercase}
  .person-role{color:var(--brand-green);font-size:16px;text-transform:uppercase;margin-bottom:8px}
  .contact{list-style:none;color:var(--ink);font-size:14px;line-height:22px}
  .contact li{display:flex;align-items:center;gap:9px}
  .contact svg{width:13px;height:13px;fill:var(--ink);flex:none}
  .band{position:absolute;bottom:0;height:12px}
  .band-blue{left:0;width:62%;background:var(--brand-blue)}
  .band-green{right:0;width:37%;background:var(--brand-green)}
</style>
</head>
<body>
  <section class="card card-back">
    <div class="brand">
      <span class="brand-dot"></span>
      <span class="brand-name">Keston Fieldworks</span>
    </div>
    <div class="social" aria-label="Social profiles">
      <span></span><span></span><span></span>
    </div>
  </section>

  <section class="card card-front">
    <div class="brand">
      <span class="brand-dot"></span>
      <span class="brand-name">Keston Fieldworks</span>
    </div>
    <div class="rule"></div>
    <div class="person">
      <p class="person-name">Dean Harlow</p>
      <p class="person-role">Director</p>
      <ul class="contact">
        <li><svg viewBox="0 0 16 16" aria-hidden="true"><path d="M3 1h3l1.5 4-2 1.3a9 9 0 0 0 4.2 4.2L11 8.5l4 1.5v3a2 2 0 0 1-2 2A12 12 0 0 1 1 3a2 2 0 0 1 2-2z"/></svg>0487305526</li>
        <li><svg viewBox="0 0 16 16" aria-hidden="true"><path d="M1 3h14v10H1z M1 3l7 6 7-6" fill="none" stroke="#555a60" stroke-width="1.6"/></svg>dean@kolvat.biz</li>
        <li><svg viewBox="0 0 16 16" aria-hidden="true"><circle cx="8" cy="8" r="7"/></svg>www.kestonfieldworks.com</li>
      </ul>
    </div>
    <div class="band band-blue"></div>
    <div class="band band-green"></div>
  </section>
</body>
</html>
```